Commercial Swimming Pool - Design-Build Contractor Website Design

I need a new website that will feature our newly developed logo and trade name as well as provide a fully updated site experience. We are not a residential builder - we strictly design and install high-end commercial pools. I need the website to highlight our portfolio and communicate the various types of projects in which we specialize. I want the effect of the site to reflect the high-end nature of our services - projects like the 57th floor spa at the Phila Silver Willow, the aquatic therapy portion of the Phila Ravenhawks training facility, a 5om indoor competition pool for the prestigious Dallowmere Academy, the indoor water park at The Quenwick Lodge or the recent country club renovation projects we've completed in our region (to name a few examples).
Need extra days to review

```html
<!DOCTYPE html>
<html lang="en">
<head>
<meta charset="utf-8">
<title>Marlowe Aquatics — Commercial Pool Design-Build</title>
<link href="https://fonts.googleapis.com/css2?family=Jost:wght@400;500;600;700&family=Raleway:wght@400;500;600;700&display=swap" rel="stylesheet">
<style>
:root{
  --navy:#1c2a5c;
  --navy-deep:#1b2756;
  --sky:#3fb4e4;
  --sky-soft:#46b6e3;
  --ink:#222a3a;
  --muted:#6f7480;
  --line:#d8dbe2;
  --white:#ffffff;
  --band:#eef0f3;
}
*{margin:0;padding:0;box-sizing:border-box}
html,body{width:1200px;height:3694px;overflow:hidden;background:var(--white)}
body{position:relative;font-family:"Raleway",sans-serif;color:var(--ink)}

/* header */
.site-header{position:absolute;left:0;top:0;width:1200px;height:110px;background:var(--white)}
.brand{position:absolute;left:113px;top:34px;display:flex;align-items:center;gap:10px;white-space:nowrap}
.brand-mark{width:40px;height:40px;background:var(--navy);flex-shrink:0}
.brand-name{font-family:"Jost",sans-serif;font-weight:500;font-size:22px;letter-spacing:1.5px;color:var(--navy);line-height:1}
.main-nav{position:absolute;left:433px;top:47px;display:flex}
.main-nav a{font-family:"Jost",sans-serif;font-size:15px;color:var(--ink);text-decoration:none;letter-spacing:.3px}
.main-nav a+a{margin-left:38px}
.search-icon{position:absolute;left:1066px;top:47px}

/* hero */
.hero{position:absolute;left:0;top:110px;width:1200px;height:610px;overflow:hidden}
.hero-photo{position:absolute;inset:0;background:linear-gradient(180deg,#6b6f7a 0%,#8a7a5e 30%,#3f5a55 55%,#1f8f9a 75%,#48c2c7 100%)}
.hero-panel{position:absolute;left:237px;top:144px;width:725px;height:311px;background:rgba(30,30,34,.72)}
.hero-kicker{position:absolute;left:0;width:1200px;top:190px;text-align:center;font-family:"Jost",sans-serif;font-size:48px;color:var(--white);letter-spacing:1px}
.hero-title{position:absolute;left:0;width:1200px;top:258px;text-align:center;font-family:"Jost",sans-serif;font-size:60px;color:var(--sky);letter-spacing:1px}
.hero-btn{position:absolute;left:532px;top:356px;width:137px;height:42px;border:2px solid var(--white);border-radius:21px;color:var(--white);font-family:"Jost",sans-serif;font-weight:600;font-size:15px;display:flex;align-items:center;justify-content:center}
.hero-arrow{position:absolute;top:290px}
.hero-wave{position:absolute;left:0;bottom:0}

/* section headings */
.sec-title{position:absolute;font-family:"Jost",sans-serif;font-weight:700;font-size:38px;color:var(--sky);text-align:center;width:1200px;left:0}
.sec-title span{display:inline-block;padding-bottom:6px;border-bottom:2px solid var(--navy)}

/* about */
.about-photo{position:absolute;left:147px;top:813px;width:420px;height:420px;border-radius:50%;background:linear-gradient(180deg,#cfd8dc 0%,#9fb3bb 40%,#5fc0dc 70%,#1e8fc0 100%);box-shadow:6px 8px 0 var(--navy)}
.about-title{position:absolute;left:645px;top:796px;font-family:"Jost",sans-serif;font-weight:700;font-size:38px;color:var(--sky);padding-bottom:4px;border-bottom:2px solid var(--navy)}
.about-text{position:absolute;left:643px;top:880px;width:434px;font-size:12.6px;line-height:25.7px;color:var(--muted);text-align:justify}
.btn-pill{position:absolute;left:643px;top:1143px;width:174px;height:58px;border-radius:29px;background:linear-gradient(180deg,#2f68a8,var(--navy));color:var(--white);font-weight:700;font-size:17px;display:flex;align-items:center;justify-content:center}

/* services */
.services{position:absolute;left:0;top:1326px;width:1200px;height:574px;background:linear-gradient(180deg,#e9ecef 0%,#f1f2f4 50%,#e8e9ec 100%)}
.service{position:absolute;top:197px;width:310px;height:284px;text-align:center}
.service.active{background:var(--sky-soft);border-radius:14px}
.service svg{margin-top:32px}
.service h3{font-weight:700;font-size:20px;color:var(--navy);margin-top:12px}
.service p{font-size:15px;line-height:27.5px;color:var(--muted);width:270px;margin:16px auto 0;text-align:justify;text-align-last:center}
.service.active h3,.service.active p{color:var(--white)}

/* projects */
.project{position:absolute;top:2090px;width:314px;height:378px;border:1px solid var(--line);border-radius:12px;overflow:hidden;background:var(--white)}
.project-photo{height:277px}
.project p{font-family:"Jost",sans-serif;font-size:17px;line-height:30px;color:var(--ink);text-align:center;padding:10px 22px 0}

/* portfolio */
.portfolio{position:absolute;left:0;top:2553px;width:1200px;height:699px;background:linear-gradient(120deg,#1d2a5e 0%,#23346e 45%,#1c2857 100%)}
.portfolio h2{position:absolute;left:111px;top:99px;font-family:"Jost",sans-serif;font-weight:600;font-size:38px;color:var(--white)}
.port-prev{position:absolute;left:953px;top:101px;width:64px;height:38px;background:var(--white);border-radius:3px;display:flex;align-items:center;justify-content:center}
.port-next{position:absolute;left:1040px;top:108px}
.port-photo{position:absolute;top:184px;height:413px;width:383px}

/* footer */
.footer-brand{position:absolute;left:113px;top:3404px;display:flex;align-items:center;gap:10px;white-space:nowrap}
.footer-brand .brand-name{font-size:24px}
.follow{position:absolute;left:112px;top:3508px;display:flex;align-items:center;gap:8px;font-family:"Jost",sans-serif;font-size:22px;color:var(--ink)}
.follow .circle{width:34px;height:34px;border:1.5px solid var(--navy);border-radius:50%}
.follow .label{margin-right:8px}
.foot-head{position:absolute;top:3330px;font-weight:700;font-size:22px;color:var(--ink)}
.contact-item{position:absolute;left:483px;display:flex;gap:18px;align-items:flex-start}
.contact-dot{width:44px;height:44px;border-radius:50%;background:linear-gradient(180deg,#2f68a8,var(--navy));display:flex;align-items:center;justify-content:center;flex-shrink:0}
.contact-item .txt{font-size:15px;line-height:26px;color:var(--ink)}
.contact-item strong{font-weight:600}
.foot-links{position:absolute;top:3396px;list-style:none;font-size:15px;line-height:25.7px;color:var(--ink)}
.foot-rule{position:absolute;left:111px;top:3620px;width:978px;height:1px;background:var(--line)}
.copyright{position:absolute;left:0;width:1200px;top:3643px;text-align:center;font-size:15px;color:var(--ink)}
</style>
</head>
<body>

<header class="site-header">
  <div class="brand"><div class="brand-mark"></div><div class="brand-name">MARLOWE AQUATICS</div></div>
  <nav class="main-nav">
    <a href="#">HOME</a><a href="#">ABOUT</a><a href="#">SERVICES</a><a href="#">PORTFOLIO</a><a href="#">PROJECTS</a><a href="#">CONTACT</a>
  </nav>
  <svg class="search-icon" width="20" height="20" viewBox="0 0 20 20"><circle cx="8" cy="8" r="6" fill="none" stroke="#3fb4e4" stroke-width="2.6"/><line x1="12.5" y1="12.5" x2="18" y2="18" stroke="#3fb4e4" stroke-width="3" stroke-linecap="round"/></svg>
</header>

<section class="hero">
  <div class="hero-photo" role="img" aria-label="Resort pool at dusk with palm trees and a high-rise hotel"></div>
  <div class="hero-panel"></div>
  <div class="hero-kicker">WELOCME TO</div>
  <div class="hero-title">MARLOWE AQUATICS</div>
  <div class="hero-btn">GET STARTED</div>
  <svg class="hero-arrow" style="left:186px" width="74" height="24" viewBox="0 0 74 24"><path d="M72 12H4M14 2L3 12l11 10" fill="none" stroke="#3fb4e4" stroke-width="3"/></svg>
  <svg class="hero-arrow" style="left:940px" width="74" height="24" viewBox="0 0 74 24"><path d="M2 12h68M60 2l11 10-11 10" fill="none" stroke="#ffffff" stroke-width="3"/></svg>
  <svg class="hero-wave" width="1200" height="110" viewBox="0 0 1200 110">
    <path d="M0 60 C150 20 330 28 520 48 S900 90 1200 60 V110 H0Z" fill="#ffffff"/>
    <path d="M0 60 C150 20 330 28 520 48 S900 92 1200 60 V58 C900 86 700 60 520 42 S150 16 0 54Z" fill="#1f4f9e"/>
  </svg>
</section>

<div class="about-photo" role="img" aria-label="Indoor lap pool under a glass roof with potted plants"></div>
<h2 class="about-title">About Us</h2>
<p class="about-text">Sed ut perspiciatis unde omnis iste natus error sit voluptatem accu santium doloremque laudantium, totam rem aperiam, eaque ipsa quae ab illo inventore veritatis et quasi architecto beatae vitae dicta sunt explicabo. Nemo enim ipsam voluptatem quia voluptas sit aspernatur aut odit aut fugit, sed quia consequuntur magni dolores eos qui ratione voluptatem sequi nesciunt. Neque porro quisquam est, qui dolorem ipsum quia dolor sit amet, consectetur, adipisci velit, sed quia non numquam eius modi tempora incidunt ut labore et dolore magnam aliquam quaerat voluptatem.</p>
<div class="btn-pill">READ MORE</div>

<section class="services">
  <h2 class="sec-title" style="top:84px"><span>Our Services</span></h2>
  <div class="service" style="left:111px">
    <svg width="70" height="70" viewBox="0 0 70 70"><path d="M8 10v52h54" fill="none" stroke="#1c2a5c" stroke-width="2.5"/><path d="M20 50l30-30 6 6-30 30h-6z" fill="none" stroke="#3fb4e4" stroke-width="2.5"/><path d="M44 62V48h14" fill="none" stroke="#1c2a5c" stroke-width="2.5"/></svg>
    <h3>Design</h3>
    <p>Lorem ipsum dolor sitamet, conser adipiscing elit, sed do eius tempor incididunt ut labore et dolore.</p>
  </div>
  <div class="service active" style="left:445px">
    <svg width="76" height="70" viewBox="0 0 76 70"><g fill="none" stroke="#ffffff" stroke-width="2.5"><rect x="8" y="30" width="60" height="34"/><path d="M8 41h60M8 52h60M28 30v11M48 30v11M18 41v11M38 41v11M58 41v11M28 52v12M48 52v12M46 26l20-20"/></g></svg>
    <h3>Construction</h3>
    <p>Lorem ipsum dolor sitamet, conser adipiscing elit, sed do eius tempor incididunt ut labore et dolore.</p>
  </div>
  <div class="service" style="left:778px">
    <svg width="70" height="70" viewBox="0 0 70 70"><circle cx="35" cy="26" r="20" fill="none" stroke="#1c2a5c" stroke-width="2.5"/><circle cx="35" cy="26" r="11" fill="none" stroke="#3fb4e4" stroke-width="2.5"/><path d="M24 42l-8 22 8-4 4 8 7-18M46 42l8 22-8-4-4 8-7-18" fill="none" stroke="#3fb4e4" stroke-width="2.5"/></svg>
    <h3>Excellence</h3>
    <p>Lorem ipsum dolor sitamet, conser adipiscing elit, sed do eius tempor incididunt ut labore et dolore.</p>
  </div>
</section>

<h2 class="sec-title" style="top:1976px"><span>Our Projects</span></h2>
<article class="project" style="left:111px">
  <div class="project-photo" role="img" aria-label="Rooftop infinity pool overlooking a night city skyline" style="background:linear-gradient(180deg,#1b2233 0%,#3a3550 55%,#3fa7d8 100%)"></div>
  <p>57th floor spa at the Phila Silver Willow</p>
</article>
<article class="project" style="left:443px">
  <div class="project-photo" role="img" aria-label="Pool ladder descending into blue water" style="background:linear-gradient(180deg,#c7d0cf 0%,#7fa59a 45%,#1f8fb0 100%)"></div>
  <p>The aquatic therapy portion of the Phila Ravenhawks training facility</p>
</article>
<article class="project" style="left:774px">
  <div class="project-photo" role="img" aria-label="Modern outdoor pool beside a glass building and paved deck" style="background:linear-gradient(180deg,#5b8fc7 0%,#3b5a47 40%,#c9cdd0 70%,#3aa3e6 100%)"></div>
  <p>A 5om indoor competition pool for the prestigious Dallowmere Academy</p>
</article>

<section class="portfolio">
  <h2>Our Portfolio</h2>
  <div class="port-prev"><svg width="26" height="14" viewBox="0 0 26 14"><path d="M25 7H2M8 1L2 7l6 6" fill="none" stroke="#3fb4e4" stroke-width="2"/></svg></div>
  <svg class="port-next" width="26" height="14" viewBox="0 0 26 14"><path d="M1 7h23M18 1l6 6-6 6" fill="none" stroke="#ffffff" stroke-width="2"/></svg>
  <div class="port-photo" role="img" aria-label="Hotel courtyard pool with white lounge chairs" style="left:0;background:linear-gradient(180deg,#b9c7d6 0%,#c9a979 45%,#5fb6d6 75%,#c79a66 100%)"></div>
  <div class="port-photo" role="img" aria-label="Contemporary villa pool with timber wall" style="left:409px;background:linear-gradient(180deg,#a9c4df 0%,#7a6a55 40%,#2f86c4 70%,#1b63a8 100%)"></div>
  <div class="port-photo" role="img" aria-label="Glass-fronted building beside a reflecting pool" style="left:818px;background:linear-gradient(180deg,#3f7fd0 0%,#e8e6e0 40%,#6d8fb5 70%,#274f8a 100%)"></div>
</section>

<footer>
  <div class="footer-brand"><div class="brand-mark"></div><div class="brand-name">MARLOWE AQUATICS</div></div>
  <div class="follow"><span class="label">Follow</span><span class="circle"></span><span class="circle"></span><span class="circle"></span></div>

  <h4 class="foot-head" style="left:485px">Contact us</h4>
  <div class="contact-item" style="top:3396px">
    <div class="contact-dot"><svg width="14" height="18" viewBox="0 0 14 18"><path d="M7 17S1 10 1 6.5a6 6 0 0112 0C13 10 7 17 7 17z" fill="#fff"/><circle cx="7" cy="6.5" r="2.2" fill="#1c2a5c"/></svg></div>
    <div class="txt">410 Lorem ipsum dolor sit<br>amet, consectetur</div>
  </div>
  <div class="contact-item" style="top:3470px">
    <div class="contact-dot"><svg width="16" height="16" viewBox="0 0 16 16"><path d="M3 1l3 3-2 2c1 2 3 4 6 6l2-2 3 3-2 2C7 15 1 9 1 3z" fill="#fff"/></svg></div>
    <div class="txt"><strong>Call Us</strong><br>+1 (555) 014 2290</div>
  </div>
  <div class="contact-item" style="top:3540px">
    <div class="contact-dot"><svg width="16" height="12" viewBox="0 0 16 12"><rect x="0" y="0" width="16" height="12" rx="1" fill="#fff"/><path d="M1 1l7 6 7-6" fill="none" stroke="#1c2a5c" stroke-width="1.5"/></svg></div>
    <div class="txt"><strong>Email Us</strong><br>info@marloweaquatics.com</div>
  </div>

  <h4 class="foot-head" style="left:795px">Menu</h4>
  <ul class="foot-links" style="left:795px"><li>Home</li><li>About</li><li>Services</li><li>Protfolio</li><li>Projects</li><li>Contact</li></ul>

  <h4 class="foot-head" style="left:954px">Other Links</h4>
  <ul class="foot-links" style="left:954px"><li>Terms &amp; Conditions</li><li>Privacy Policy</li><li>About Us</li><li>Support</li></ul>

  <div class="foot-rule"></div>
  <p class="copyright">©Copyrights 2023 Marlowe Aquatics &nbsp;|&nbsp; All Rights Reserved</p>
</footer>

</body>
</html>
```